Poster for a Bicycle show/Expo

We need a poster for a Bicycle show/Expo and sustainable transport. Exhibitors will sell bikes, cycling clothing, accessories, etc. ...
This show is annual and the Poster is for the 2015 edition.

The style must be modern, dynamic, bright colors.

Your concept must be compatible in a landscape format. (We will ourselves adaptations of different formats.)
Width: 210 mm
Height: 297 mm
It's necessary for us to have the source file (vector) for make, later, the different format (flyers, website, ...)

Content of the Poster:
- 1 big picture (no clip art)
- Big title: « Foire du Rayon » (« Salon » or « Salon du » can be small and « Vélo » big.)
- Subtitle: « et de la mobilité douce »
- Date: « 8, 9 et 10 mai 2015 » or « 8-10 mai 2015 »
- Place: « Halle TRV - Gare de Lunel »
- Text line 1: « www.foire-du-rayon.ch - Entrée gratuite »
- Text line 2« Piste d’essais - Restauration sur place »
- Text line 3: « Ve 8 mai de 17h à 21h - Sa 9 mai de 10h à 20h - Di 10 mai de 10h à 18h »
- Please, leave a zone in the poster for sponsors logos
(The predominant information (most visible) are: « Foire du Rayon » and « 8, 9 et 10 mai 2015 or 8-10 mai 2015 »)

Content of the big picture:
- from a cheap stock, like PixKiosk.com
- a bicycle in action or a detail of a bicycle (or a accessory) (no race bike)
- a modern picture with bright colors.
- if a person is on the picture, we prefer a men
- not an aerial view with cyclists in a landscape.

Some examples of poster of shows - with typo-title worked

http://www.expobassinlutece.com/Temp/IMG/F_a9b3c2d4e5f60718293a4b5c6d7e8f9012345678901_200_296.png

http://qx4m.tornafoire.fr/Data/pvtorn_mer/block/F_7cc1bb9396aef1d5e69283647561f0076457c357c5ea6.pdf
(page 2 of this PDF)

http://salons.rivol-evenements.fr/images/rivol-evenements/foires-salons/phototheque/salon-auto-bourlac/salon-auto-bourlac2012-affiche.jpg

http://www.tirovel.net/blog/wp-content/uploads/2007/03/affiche-salon-du-livre.jpg

http://www.quaimarin-gens.com/wp-content/affiche-cannes-2007.jpg
Updates

Hello,

For information, for your next versions, please, add the text "Piste d'essais".

- Text line 1: « www.foire-du-rayon.ch - Entrée gratuite »
- Text line 2: « Piste d’essais - Restauration sur place »
- Text line 3: « Ve 8 mai de 17h à 21h - Sa 9 mai de 10h à 20h - Di 10 mai de 10h à 18h »

Thanks,
Rodolphe

```html
<!DOCTYPE html>
<html lang="fr">
<head>
<meta charset="utf-8">
<title>Foire du Rayon 2015 – Affiche</title>
<link rel="stylesheet" href="https://fonts.googleapis.com/css2?family=Bebas+Neue&family=Oswald:wght@500;600&display=swap">
<style>
  :root {
    --page-bg: #e4e4e4;
    --paper: #ffffff;
    --ink: #111111;
    --lime: #b3c71a;
    --teal: #5cbec7;
    --bar: #333333;
    --white: #ffffff;
    --photo-light: #f4f5f6;
    --photo-mid: #c9cdd1;
    --photo-dark: #4a4d50;
  }
  * { margin: 0; padding: 0; box-sizing: border-box; }
  html, body { width: 1200px; height: 1152px; overflow: hidden; }
  body { background: var(--page-bg); position: relative; }

  .poster {
    position: absolute; left: 40px; top: 180px;
    width: 1120px; height: 792px;
    background: var(--paper);
    overflow: hidden;
  }

  .hero-photo {
    position: absolute; left: 620px; top: 0;
    width: 500px; height: 666px;
    background:
      radial-gradient(ellipse at 65% 45%, var(--photo-mid) 0%, transparent 60%),
      linear-gradient(135deg, var(--photo-light) 0%, var(--photo-mid) 55%, var(--photo-dark) 100%);
  }

  .title-kicker {
    position: absolute; left: 64px; top: 52px;
    font-family: "Bebas Neue", sans-serif;
    font-size: 56px; line-height: 1; color: var(--ink);
    letter-spacing: 1px;
  }
  .title-main {
    position: absolute; left: 60px; top: 96px;
    font-family: "Bebas Neue", sans-serif;
    font-size: 250px; line-height: 0.9; color: var(--ink);
    letter-spacing: 4px;
    white-space: nowrap;
    transform: scaleY(1.2); transform-origin: top left;
  }
  .title-side {
    position: absolute; left: 578px; top: 218px;
    transform: translate(-50%, -50%) rotate(-90deg);
    font-family: "Bebas Neue", sans-serif;
    font-size: 44px; line-height: 1; color: var(--ink);
    white-space: nowrap; letter-spacing: 0.5px;
  }

  .band {
    position: absolute; left: 0;
    color: var(--white);
    font-family: "Oswald", sans-serif; font-weight: 500;
    text-transform: uppercase;
    padding-left: 88px;
  }
  .band-subtitle {
    top: 384px; width: 560px; height: 62px;
    background: var(--lime);
    font-size: 33px; line-height: 62px;
  }
  .band-event {
    top: 464px; width: 476px; height: 92px;
    background: var(--teal);
    font-size: 31px; line-height: 38px;
    padding-top: 8px;
  }

  .opening-hours {
    position: absolute; left: 88px; top: 576px;
    font-family: "Oswald", sans-serif; font-weight: 500;
    font-size: 12px; color: var(--teal);
    text-transform: uppercase; white-space: nowrap;
  }

  .info-bar {
    position: absolute; left: 0; top: 670px;
    width: 100%; height: 32px;
    background: var(--bar); color: var(--white);
    font-family: "Oswald", sans-serif; font-weight: 500;
    font-size: 17px; line-height: 32px; text-align: center;
    text-transform: uppercase;
  }

  .sponsors {
    position: absolute; left: 0; top: 702px;
    width: 100%; height: 90px;
    display: flex; justify-content: space-around; align-items: center;
    padding: 0 30px;
    list-style: none;
  }
  .sponsor {
    font-family: "Oswald", sans-serif; font-weight: 600;
    font-size: 26px; color: var(--ink);
    text-transform: uppercase; letter-spacing: 1px;
    width: 150px; text-align: center;
  }
</style>
</head>
<body>
  <main class="poster">
    <div class="hero-photo" role="img" aria-label="Gros plan sur la roue avant et le frein d’un vélo argenté sur fond blanc"></div>

    <h1>
      <span class="title-kicker">Foire du</span>
      <span class="title-main">RAYON</span>
    </h1>
    <p class="title-side">Piste d’essais</p>

    <p class="band band-subtitle">Et de la mobilité douce</p>
    <p class="band band-event">8-10 mai 2015<br>Halle TRV - Gare de Lunel</p>

    <p class="opening-hours">Ve 8 mai de 17h à 21h &nbsp;•&nbsp; Sa 9 mai de 10h à 20h &nbsp;•&nbsp; Di 10 mai de 10h à 18h</p>

    <p class="info-bar">www.foire-du-rayon.ch - Entrée gratuite - Restauration sur place</p>

    <ul class="sponsors">
      <li class="sponsor">Vantek</li>
      <li class="sponsor">Corsina</li>
      <li class="sponsor">Rolda</li>
      <li class="sponsor">Driva</li>
      <li class="sponsor">Corsina</li>
      <li class="sponsor">Rolda</li>
    </ul>
  </main>
</body>
</html>
```